Heavy Duty Repairs Poster

Good afternoon - I'm looking for a poster , design to set up around different areas. The Poster must consist of the following
- Heavy duty repairs
- Pictures of Semi trucks , heavy construction equipment , trailers
- Agriculture
- All north American equipment ( see attached pictures)
- Brief Descriptions in bullet point forms
CVIPS
WELDING
AIR CONDITIONING
ENGINE REBUILDS
DIAGONSTICS
FLEET MANAGMENT
TIRE REPAIR AND SALES
ELECTRICAL , HYDRALIC , POWER TRAIN SERVICE AND REPAIRS
PART SALES
FLEET MAINTINACE
DELTEING AND TUNING
AFTER MARKET INSTALLS OUTFITTING
ONSITE & OFFSITE REPAIRS
FULL RECERTIFACTION OVERHAULING
Warranty Approved

Target Market(s)

Heavy Duty Truck , Equipment , Agriculture Owners

Industry/Entity Type

Heavy Duty Repairs

Colors
EB3D1F
EC4F4E
F09395
F8D3D4
FCEDEE

Requirements
Must have
• Pictures of : Semi trucks and trailer , Construction heavy equipment , agriculture equipment
Nice to have
• Flashy and stands out

```html
<!DOCTYPE html>
<html lang="en">
<head>
<meta charset="utf-8">
<title>Heavy Duty Equipment Repairs Poster</title>
<link href="https://fonts.googleapis.com/css2?family=Graduate&family=Alfa+Slab+One&family=Tinos:wght@400;700&display=swap" rel="stylesheet">
<style>
  :root {
    --red: #eb3d1f;
    --red-bright: #ec1c24;
    --red-soft: #ec4f4e;
    --pink: #f09395;
    --blush: #f8d3d4;
    --paper: #f4f4f4;
    --ink: #0b0b0b;
    --panel: #4a4a4a;
    --panel-dark: #2c2c2c;
    --steel-light: #f2f2f2;
    --steel-dark: #8c8c8c;
    --gold: #d4a93a;
    --white: #ffffff;
  }
  * { margin: 0; padding: 0; box-sizing: border-box; }
  html, body { width: 1200px; height: 2844px; overflow: hidden; background: var(--paper); }
  .poster {
    position: absolute; left: 50px; top: 643px; width: 1100px; height: 1558px;
    background:
      radial-gradient(ellipse at 0% 0%, #7a0d0d 0%, transparent 45%),
      radial-gradient(ellipse at 100% 0%, #7a0d0d 0%, transparent 45%),
      radial-gradient(ellipse at 100% 85%, #5a0a0a 0%, transparent 35%),
      var(--ink);
    overflow: hidden;
    box-shadow: 0 20px 50px rgba(0,0,0,0.25);
  }
  .poster__plate { position: absolute; inset: 0; }
  .headline { position: absolute; left: 0; right: 0; top: 48px; text-align: center; font-family: "Graduate", serif; }
  .headline__top { font-size: 58px; color: var(--steel-light); letter-spacing: 2px; line-height: 1; transform: skewX(-8deg); }
  .headline__mid {
    font-family: "Alfa Slab One", serif; font-size: 112px; line-height: 1.05; margin-top: 6px;
    background: linear-gradient(180deg, var(--steel-light) 0%, var(--steel-dark) 55%, #d9d9d9 100%);
    -webkit-background-clip: text; background-clip: text; color: transparent;
    transform: skewX(-8deg);
  }
  .headline__main {
    font-family: "Alfa Slab One", serif; font-size: 146px; line-height: 1; margin-top: -4px;
    color: var(--red-bright); transform: skewX(-10deg);
    text-shadow: 0 6px 0 #8e0d0d;
  }
  .truck-photo {
    position: absolute; left: 250px; top: 380px; width: 850px; height: 560px;
    background: linear-gradient(160deg, #5a1a14 0%, #b0281e 35%, #8a3a24 60%, #2a0c08 100%);
    clip-path: polygon(0 30%, 55% 0, 100% 10%, 100% 100%, 0 100%);
    opacity: 0.95;
  }
  .approval-seal {
    position: absolute; left: 73px; top: 670px; width: 232px; height: 232px; border-radius: 50%;
    background: radial-gradient(circle, var(--ink) 0 52%, var(--gold) 53% 100%);
    box-shadow: 0 0 0 6px #8e6a1c inset;
  }
  .services {
    position: absolute; left: 80px; top: 960px; width: 960px;
    display: grid; grid-template-columns: repeat(5, 1fr); row-gap: 22px;
  }
  .service {
    display: flex; flex-direction: column; align-items: center; text-align: center;
    border-right: 2px dashed #555; height: 122px;
  }
  .service:nth-child(5n) { border-right: none; }
  .service__icon {
    width: 82px; height: 82px; border-radius: 50%; background: var(--red-bright);
    border: 4px solid var(--white); display: flex; align-items: center; justify-content: center;
    box-shadow: 0 0 0 3px #888;
  }
  .service__icon svg { width: 46px; height: 46px; }
  .service__label {
    margin-top: 8px; font-family: "Alfa Slab One", serif; font-size: 16px; line-height: 1;
    color: var(--blush); text-transform: uppercase; transform: skewX(-10deg);
  }
  .contact-card {
    position: absolute; left: 91px; top: 1420px; width: 234px; height: 104px; background: #050505;
    display: flex; flex-direction: column; align-items: center; justify-content: center; gap: 8px;
  }
  .contact-card__phone { font-family: "Alfa Slab One", serif; font-size: 25px; color: var(--red-soft); letter-spacing: 1px; }
  .contact-card__name { font-family: "Tinos", serif; font-size: 16px; color: var(--white); }
  .contact-card__place { font-family: "Tinos", serif; font-size: 12px; color: var(--white); margin-top: -6px; }
  .web-bar {
    position: absolute; left: 358px; top: 1438px; width: 760px; height: 74px;
    background: var(--red-bright); border-radius: 37px 0 0 37px;
    display: flex; align-items: center; padding-left: 40px;
    font-family: "Alfa Slab One", serif; font-size: 25px; color: var(--white); letter-spacing: 2px;
  }
</style>
</head>
<body>
<main class="poster">
  <svg class="poster__plate" viewBox="0 0 1100 1558" aria-hidden="true">
    <defs>
      <linearGradient id="plateFill" x1="0" y1="0" x2="0" y2="1">
        <stop offset="0" stop-color="#555"/>
        <stop offset="1" stop-color="#2f2f2f"/>
      </linearGradient>
    </defs>
    <polygon points="200,0 900,0 1045,150 1045,240 550,580 55,240 55,150" fill="url(#plateFill)"/>
  </svg>

  <header class="headline">
    <div class="headline__top">HEAVY DUTY</div>
    <div class="headline__mid">EQUIPMENT</div>
    <div class="headline__main">REPAIRS</div>
  </header>

  <div class="truck-photo" role="img" aria-label="Photo of a red semi truck hauling a rust-orange container trailer"></div>
  <div class="approval-seal" role="img" aria-label="Gold warranty approved seal"></div>

  <section class="services">
    <div class="service"><div class="service__icon"><svg viewBox="0 0 24 24" fill="none" stroke="#fff" stroke-width="2"><rect x="4" y="3" width="16" height="18" rx="2"/><path d="M8 12l3 3 5-6"/></svg></div><div class="service__label">CVIPS</div></div>
    <div class="service"><div class="service__icon"><svg viewBox="0 0 24 24" fill="none" stroke="#fff" stroke-width="2"><path d="M4 20l8-8M12 12l3-6 5 5-6 3z"/><path d="M5 8l1-2M8 5l2-1"/></svg></div><div class="service__label">WELDING</div></div>
    <div class="service"><div class="service__icon"><svg viewBox="0 0 24 24" fill="none" stroke="#fff" stroke-width="2"><circle cx="12" cy="12" r="9"/><path d="M12 7v5l3 2"/></svg></div><div class="service__label">AIR<br>CONDITIONING</div></div>
    <div class="service"><div class="service__icon"><svg viewBox="0 0 24 24" fill="none" stroke="#fff" stroke-width="2"><circle cx="12" cy="12" r="9"/><circle cx="12" cy="12" r="3"/><path d="M12 3v6M12 15v6M3 12h6M15 12h6"/></svg></div><div class="service__label">ENGINE<br>REBUILDS</div></div>
    <div class="service"><div class="service__icon"><svg viewBox="0 0 24 24" fill="none" stroke="#fff" stroke-width="2"><rect x="3" y="8" width="18" height="10" rx="1"/><circle cx="7" cy="19" r="2"/><circle cx="17" cy="19" r="2"/><path d="M13 10l-2 3h3l-2 3"/></svg></div><div class="service__label">DIAGONSTICS</div></div>

    <div class="service"><div class="service__icon"><svg viewBox="0 0 24 24" fill="none" stroke="#fff" stroke-width="2"><path d="M12 3l6 2v5c0 4-3 6-6 7-3-1-6-3-6-7V5z"/><path d="M9 10l2 2 4-4"/></svg></div><div class="service__label">FLEET<br>MANAGMENT</div></div>
    <div class="service"><div class="service__icon"><svg viewBox="0 0 24 24" fill="none" stroke="#fff" stroke-width="2"><rect x="3" y="6" width="18" height="7" rx="1"/><path d="M7 16v4M11 16v4M15 16v4"/></svg></div><div class="service__label">PART<br>SALES</div></div>
    <div class="service"><div class="service__icon"><svg viewBox="0 0 24 24" fill="none" stroke="#fff" stroke-width="2"><rect x="3" y="3" width="8" height="6" rx="1"/><path d="M10 20l8-8M15 9l4-4"/></svg></div><div class="service__label">FLEET<br>MAINTINACE</div></div>
    <div class="service"><div class="service__icon"><svg viewBox="0 0 24 24" fill="none" stroke="#fff" stroke-width="2"><circle cx="12" cy="12" r="4"/><path d="M12 2v4M12 18v4M2 12h4M18 12h4M5 5l3 3M16 16l3 3M5 19l3-3M16 8l3-3"/></svg></div><div class="service__label">TIRE REPAIR<br>AND SALES</div></div>
    <div class="service"><div class="service__icon"><svg viewBox="0 0 24 24" fill="none" stroke="#fff" stroke-width="2"><path d="M4 6h16M9 6V4h6v2M6 6l1 14h10l1-14M10 10v7M14 10v7"/></svg></div><div class="service__label">ELECTRICAL<br>HYDRALIC</div></div>

    <div class="service"><div class="service__icon"><svg viewBox="0 0 24 24" fill="none" stroke="#fff" stroke-width="2"><path d="M3 15l2-5h14l2 5v3H3z"/><circle cx="7" cy="18" r="2"/><circle cx="17" cy="18" r="2"/></svg></div><div class="service__label">POWER TRAIN<br>SERVICE &amp; REPAIRS</div></div>
    <div class="service"><div class="service__icon"><svg viewBox="0 0 24 24" fill="none" stroke="#fff" stroke-width="2.4"><path d="M4 20L20 4M4 4l16 16"/></svg></div><div class="service__label">DELTEING<br>&amp; TUNING</div></div>
    <div class="service"><div class="service__icon"><svg viewBox="0 0 24 24" fill="none" stroke="#fff" stroke-width="2"><circle cx="12" cy="12" r="9"/><path d="M13 5l-4 8h4l-2 6"/></svg></div><div class="service__label">ONSITE &amp;<br>OFFSITE<br>REPAIRS</div></div>
    <div class="service"><div class="service__icon"><svg viewBox="0 0 24 24" fill="none" stroke="#fff" stroke-width="2"><path d="M3 9h18l-2-5H5z"/><rect x="5" y="9" width="14" height="11"/><path d="M9 20v-5h6v5"/></svg></div><div class="service__label">FULL<br>RECERTIFACTION<br>OVERHAULING</div></div>
    <div class="service"><div class="service__icon"><svg viewBox="0 0 24 24" fill="none" stroke="#fff" stroke-width="2.2"><path d="M5 19L19 5M5 5l14 14M16 3l5 5M3 16l5 5"/></svg></div><div class="service__label">AFTER MARKET<br>INSTALLS<br>OUTFITTING</div></div>
  </section>

  <div class="contact-card">
    <div class="contact-card__phone">780-555-0148</div>
    <div class="contact-card__name">Ridgeline Heavy Repair</div>
    <div class="contact-card__place">Maple Ford, Alberta</div>
  </div>
  <div class="web-bar">WWW.RIDGELINEHEAVYREPAIR.COM</div>
</main>
</body>
</html>
```